Harbor Ledger Funds Bus card and Logo

I need a logo design and Bus card design. The fund focuses on evaluating and investing in minerals (sub-surface rights) and real estate.

Harbor ledger refers to a book of knowledge that each plebe gets when entering the Kelmont Marine Academy (my alma mater)

Target Market(s)

Investors and financial advisors

Contact Information for Business Card

Simple - perhaps a logo with a theme on book of knowledge

Logo Text

Ex Scientia Imperium

Font styles to use
Serif
Sans Serif

Colors

Designer to choose colors to be used in the design.

Requirements
Must have
• memorable logo that is relatively simple

```html
<!DOCTYPE html>
<html lang="en">
<head>
<meta charset="utf-8">
<title>Harbor Ledger Funds – Business Card</title>
<link rel="stylesheet" href="https://fonts.googleapis.com/css2?family=Montserrat:wght@600&family=Roboto:wght@500&family=Work+Sans:wght@400&display=swap">
<style>
  :root {
    --backdrop: #1b1b1d;
    --navy: #163a66;
    --sky: #12a6e8;
    --paper: #ffffff;
    --ink: #1c2a44;
  }
  html, body {
    margin: 0;
    padding: 0;
    width: 1200px;
    height: 897px;
    overflow: hidden;
    background: var(--backdrop);
  }
  .canvas {
    position: relative;
    width: 1200px;
    height: 897px;
  }
  .card {
    position: absolute;
    left: 303px;
    width: 595px;
    height: 338px;
    overflow: hidden;
    box-shadow: 0 6px 18px rgba(0,0,0,0.55);
  }
  .card--front { top: 92px; background: var(--paper); }
  .card--back { top: 469px; background: var(--navy); }

  .brand {
    position: absolute;
    font-family: "Montserrat", sans-serif;
    font-weight: 600;
    text-align: center;
    line-height: 1.15;
    letter-spacing: 0.5px;
  }
  .card--front .brand {
    left: 20px;
    width: 275px;
    top: 135px;
    font-size: 24px;
    color: var(--navy);
  }
  .card--back .brand {
    left: 0;
    width: 595px;
    top: 178px;
    font-size: 34px;
    color: var(--paper);
  }

  .divider {
    position: absolute;
    left: 305px;
    top: 90px;
    width: 1.5px;
    height: 160px;
    background: var(--navy);
  }
  .contact {
    position: absolute;
    left: 336px;
    top: 84px;
    font-family: "Work Sans", sans-serif;
    color: var(--ink);
    font-size: 15px;
  }
  .contact__name {
    margin: 0;
    font-family: "Roboto", sans-serif;
    font-weight: 500;
    font-size: 29px;
    line-height: 1;
    color: var(--sky);
    letter-spacing: -0.3px;
  }
  .contact__role { margin: 4px 0 0; font-size: 15px; }
  .contact__address { margin: 16px 0 0; line-height: 19px; }
  .contact__list {
    list-style: none;
    margin: 10px 0 0;
    padding: 0;
    line-height: 20px;
  }
  .contact__list li { display: flex; align-items: center; gap: 6px; }
  .contact__list svg { width: 10px; height: 10px; flex: none; }

  .wave { position: absolute; left: 0; bottom: 0; width: 595px; height: 80px; }
</style>
</head>
<body>
<main class="canvas">
  <section class="card card--front">
    <div class="brand">HARBOR LEDGER<br>FUNDS LLC</div>
    <div class="divider"></div>
    <div class="contact">
      <h1 class="contact__name">DANIEL WHITFORD</h1>
      <p class="contact__role">Director</p>
      <p class="contact__address">1187 Cedar Hollow Lane<br>Brookvale, CA 95412</p>
      <ul class="contact__list">
        <li><svg viewBox="0 0 10 10" aria-hidden="true"><path d="M2 1l2 2-1 1.3c.6 1.3 1.4 2.1 2.7 2.7L7 6l2 2-1.2 1.3C4.5 9 1 5.5.7 2.2z" fill="var(--sky)"/></svg>+330 5172-4036</li>
        <li><svg viewBox="0 0 10 10" aria-hidden="true"><rect x="0.7" y="2" width="8.6" height="6" fill="none" stroke="var(--sky)" stroke-width="1"/><path d="M0.7 2l4.3 3.3L9.3 2" fill="none" stroke="var(--sky)" stroke-width="1"/></svg>info@harborledgerfunds.com</li>
        <li><svg viewBox="0 0 10 10" aria-hidden="true"><circle cx="5" cy="5" r="4.2" fill="none" stroke="var(--sky)" stroke-width="1"/><path d="M1 5h8M5 .8c-2.2 2.6-2.2 5.8 0 8.4M5 .8c2.2 2.6 2.2 5.8 0 8.4" fill="none" stroke="var(--sky)" stroke-width="0.8"/></svg>www.harborledgerfunds.com</li>
      </ul>
    </div>
    <svg class="wave" viewBox="0 0 595 80" preserveAspectRatio="none" aria-hidden="true">
      <path d="M0 22 C90 -4 200 6 320 30 C430 50 520 48 595 22 L595 80 L0 80 Z" fill="var(--sky)"/>
      <path d="M0 37 C80 8 200 18 320 38 C440 58 530 50 595 32 L595 80 L0 80 Z" fill="var(--paper)"/>
      <path d="M0 42 C80 14 200 24 320 42 C440 60 530 54 595 36 L595 80 L0 80 Z" fill="var(--navy)"/>
    </svg>
  </section>

  <section class="card card--back">
    <div class="brand">HARBOR LEDGER<br>FUNDS LLC</div>
  </section>
</main>
</body>
</html>
```